Business card for Crestline Bathrooms

Please design a business card for our bathroom renovation business. You can use my existing logo, but if you have an idea to modernize it, I would like to see it. Please see attached files first. I would like to use the blue and the orange theme. I like the concept of using the shower head in the logo. Please find following a design (or two) that I have been trying to create with my limited resources. That design was for a sign, but I was going to adopt it and use it as a business card as well. I like the concept of the water splash but I don’t think it “flows” nicely together with the logo. Another thought is that maybe creating the logo out of water splash could work and have a dramatic effect (like the water text and the butterfly picture attached with similar background instead of white). If the above doesn’t work I would like to see a modern simplified design. One of the attached files named as the unwanted business card has all the details that I want included in the business card. Please note that it is two sided.
Updates

I am very thankful for the designs that I have received, but they are very similar and only a couple of attempts to do something with the water splash as per my original brief. Modernizing the logo and having it made out of out of water splash with the orange as color accent could work and have a dramatic effect (like the water text and the butterfly picture attached with similar background instead of white). Please do not use the butterfly itself! This is just an example that images can be created out of water splash.

Contact Information for Business Card

all the details are on the unwonted business card file included

Colors
3176b5

Requirements
Nice to have
• Copied from the brief:
• ... maybe creating the logo out of water splash could work and have a dramatic effect (like the water text and the butterfly picture attached with similar background instead of white). Please do not use the butterfly itself!
Should not have
• I am getting designs with a butterfly. The butterfly picture was an example of creating something from a water splash. The butterfly itself has no association with anything other than the concept of creating a logo out of water splash. Sorry, I thought I was clear in the brief.

```html
<!DOCTYPE html>
<html lang="en">
<head>
<meta charset="utf-8">
<title>Crestline Bathrooms – Business Card</title>
<link rel="stylesheet" href="https://fonts.googleapis.com/css2?family=Montserrat:wght@400;500;600;700&display=swap">
<style>
  :root {
    --navy: #0f4373;
    --navy-deep: #0b355d;
    --water: #3176b5;
    --water-light: #6aa3d6;
    --coral: #ec7868;
    --white: #ffffff;
    --backdrop: #3a3c40;
  }
  * { margin: 0; padding: 0; box-sizing: border-box; }
  html, body { width: 1200px; height: 900px; overflow: hidden; }
  body {
    background: var(--backdrop);
    font-family: "Montserrat", sans-serif;
    display: flex;
    align-items: center;
    justify-content: center;
    gap: 30px;
  }
  .card {
    position: relative;
    width: 560px;
    height: 342px;
    border-radius: 22px;
    overflow: hidden;
    box-shadow: 0 10px 30px rgba(0,0,0,0.35);
  }
  /* front */
  .card--front { background: var(--white); }
  .card__art { position: absolute; inset: 0; }
  .brand {
    position: absolute;
    display: flex;
    align-items: center;
    gap: 10px;
    color: var(--navy);
    font-weight: 600;
    font-size: 25px;
    letter-spacing: 0.3px;
  }
  .brand__dot {
    width: 14px; height: 14px;
    border-radius: 50%;
    background: var(--coral);
  }
  .card--front .brand { left: 34px; top: 52px; }
  .memberships {
    position: absolute;
    right: 30px; top: 26px;
    display: flex; align-items: center; gap: 16px;
  }
  .memberships__badge { width: 38px; height: 38px; border-radius: 50%; background: var(--navy); }
  .memberships__divider { width: 1px; height: 30px; background: var(--navy); }
  .memberships__badge--square { width: 106px; height: 32px; border-radius: 4px; }
  .contact {
    position: absolute;
    right: 30px; top: 198px;
    text-align: right;
    color: var(--white);
  }
  .contact__name {
    font-size: 21px; font-weight: 600;
    line-height: 26px;
    letter-spacing: 0.5px; text-transform: uppercase;
    margin-bottom: 8px;
  }
  .contact__line {
    font-size: 14px; font-weight: 400;
    line-height: 19px;
    display: flex; justify-content: flex-end; align-items: center; gap: 8px;
  }
  .contact__icon { width: 13px; height: 13px; fill: none; stroke: var(--white); stroke-width: 1.6; }
  .contact__address { margin-bottom: 5px; }
  /* back */
  .card--back {
    background: var(--navy);
    display: flex; flex-direction: column; align-items: center; justify-content: center;
    gap: 30px;
  }
  .card--back .brand { position: static; color: var(--white); font-size: 28px; }
  .services {
    list-style: none;
    text-align: center;
    color: var(--white);
    font-size: 13px; font-weight: 600;
    line-height: 23px;
    text-transform: uppercase;
    letter-spacing: 0.4px;
  }
  .services li::before { content: "> "; font-weight: 400; }
</style>
</head>
<body>
  <section class="card card--front">
    <svg class="card__art" viewBox="0 0 560 342" width="560" height="342">
      <defs>
        <linearGradient id="waterFill" x1="0" y1="0" x2="1" y2="1">
          <stop offset="0" stop-color="var(--water-light)"/>
          <stop offset="0.45" stop-color="var(--water)"/>
          <stop offset="1" stop-color="var(--navy-deep)"/>
        </linearGradient>
      </defs>
      <path role="img" aria-label="Water splash photograph" fill="url(#waterFill)"
            d="M0,160 C80,210 160,215 230,202 C330,182 440,115 560,90 L560,342 L0,342 Z"/>
      <path fill="var(--navy)" d="M0,95 C12,150 60,190 130,205 C60,203 16,182 0,158 Z"/>
      <path fill="none" stroke="var(--coral)" stroke-width="5"
            d="M0,150 C80,200 160,205 230,192 C330,172 440,105 560,80"/>
    </svg>
    <div class="brand"><span class="brand__dot"></span>Crestline Bathrooms</div>
    <div class="memberships">
      <span class="memberships__badge"></span>
      <span class="memberships__divider"></span>
      <span class="memberships__badge memberships__badge--square"></span>
    </div>
    <div class="contact">
      <p class="contact__name">Daniel Petrovski</p>
      <div class="contact__address">
        <p class="contact__line">PO Box 41</p>
        <p class="contact__line">Kingsford Park 2740</p>
      </div>
      <p class="contact__line">0400 555 218 | 6200 4417
        <svg class="contact__icon" viewBox="0 0 16 16"><path d="M4 1.5l2.5 3-1.5 2a9 9 0 0 0 4.5 4.5l2-1.5 3 2.5-1.5 2.5C7 14 2 9 1.5 3z"/></svg>
      </p>
      <p class="contact__line">daniel@crestlinebathrooms.com.au
        <svg class="contact__icon" viewBox="0 0 16 16"><rect x="1.5" y="3.5" width="13" height="9"/><path d="M1.5 3.5L8 9l6.5-5.5"/></svg>
      </p>
      <p class="contact__line">www.crestlinebathrooms.com.au
        <svg class="contact__icon" viewBox="0 0 16 16"><circle cx="8" cy="8" r="6.5"/><path d="M1.5 8h13M8 1.5c-3 3.5-3 9.5 0 13M8 1.5c3 3.5 3 9.5 0 13"/></svg>
      </p>
    </div>
  </section>

  <section class="card card--back">
    <div class="brand"><span class="brand__dot"></span>Crestline Bathrooms</div>
    <ul class="services">
      <li>Complete bathroom renovations &amp; remodelling</li>
      <li>Highly skilled &amp; qualified tradespeople</li>
      <li>Professional service from concept to completion</li>
      <li>All work guaranteed</li>
    </ul>
  </section>
</body>
</html>
```